Accounting firm needing business card / letterhead designed
Marcus L. Trenholm, CPA
marcus@veltrowledger.com
www.veltrowledger.com
842 E Alder Ave Halden Falls, MN 43827
419-562-0974

```html
<!DOCTYPE html>
<html lang="en">
<head>
<meta charset="utf-8">
<title>Veltro Ledger – Business Card</title>
<link rel="stylesheet" href="https://fonts.googleapis.com/css2?family=Jura:wght@600;700&family=Roboto:wght@400&display=swap">
<style>
  :root {
    --stage: #141414;
    --navy: #29245f;
    --navy-deep: #2a2366;
    --violet: #3f3794;
    --green: #8cc63f;
    --paper-light: #f7f7f7;
    --paper-shade: #e9e9e9;
    --ink: #4a4a4a;
    --icon-cut: #eeeeee;
  }
  * { box-sizing: border-box; }
  html, body {
    margin: 0;
    width: 1200px;
    height: 960px;
    overflow: hidden;
    background: var(--stage);
  }
  .canvas {
    position: relative;
    width: 1200px;
    height: 960px;
  }
  .card {
    position: absolute;
    width: 600px;
    height: 343px;
  }
  .card-front {
    left: 302px;
    top: 129px;
    background: linear-gradient(90deg, var(--paper-light) 0%, var(--paper-shade) 100%);
  }
  .brand-name {
    position: absolute;
    left: 40px;
    top: 48px;
    margin: 0;
    font-family: "Jura", sans-serif;
    font-weight: 700;
    font-size: 40px;
    letter-spacing: 1px;
    line-height: 1;
    color: var(--navy);
    white-space: nowrap;
  }
  .holder-name {
    position: absolute;
    right: 38px;
    top: 196px;
    margin: 0;
    font-family: "Jura", sans-serif;
    font-weight: 700;
    font-size: 24px;
    line-height: 30px;
    letter-spacing: 0.3px;
    color: var(--navy);
    white-space: nowrap;
  }
  .contact-list {
    position: absolute;
    right: 38px;
    top: 234px;
    margin: 0;
    padding: 0;
    list-style: none;
    font-family: "Roboto", sans-serif;
    font-size: 14.5px;
    color: var(--ink);
  }
  .contact-item {
    display: flex;
    justify-content: flex-end;
    align-items: center;
    height: 20px;
    gap: 8px;
    white-space: nowrap;
  }
  .contact-icon {
    width: 14px;
    height: 14px;
    fill: var(--navy);
    flex: none;
  }
  .accent-green {
    position: absolute;
    right: 0;
    top: 199px;
    width: 10px;
    height: 34px;
    background: var(--green);
  }
  .accent-navy {
    position: absolute;
    right: 0;
    top: 235px;
    width: 10px;
    height: 74px;
    background: var(--navy);
  }
  .card-back {
    left: 299px;
    top: 488px;
    background: linear-gradient(160deg, var(--violet) 0%, var(--navy-deep) 55%, #2b2468 100%);
  }
</style>
</head>
<body>
<main class="canvas">
  <section class="card card-front">
    <h1 class="brand-name">VELTRO LEDGER</h1>
    <h2 class="holder-name">Marcus L. Trenholm, CPA</h2>
    <ul class="contact-list">
      <li class="contact-item">
        <span>555-562-0974</span>
        <svg class="contact-icon" viewBox="0 0 24 24" aria-hidden="true"><path d="M6.6 10.8a15.1 15.1 0 0 0 6.6 6.6l2.2-2.2a1 1 0 0 1 1-.25 11.4 11.4 0 0 0 3.6.57 1 1 0 0 1 1 1V20a1 1 0 0 1-1 1A17 17 0 0 1 3 4a1 1 0 0 1 1-1h3.5a1 1 0 0 1 1 1c0 1.250.2 2.450.57 3.570a1 1 0 0 1-.25 1z"/></svg>
      </li>
      <li class="contact-item">
        <span>marcus@veltrowledger.com</span>
        <svg class="contact-icon" viewBox="0 0 24 24" aria-hidden="true"><path d="M2 5h20v14H2z"/><path d="M3 6l9 7 9-7" fill="none" stroke="var(--icon-cut)" stroke-width="1.6"/></svg>
      </li>
      <li class="contact-item">
        <span>www.veltrowledger.com</span>
        <svg class="contact-icon" viewBox="0 0 24 24" aria-hidden="true"><circle cx="12" cy="12" r="10"/><path d="M7 6c2 1 1 3 3 4s0 3 2 4-1 4 1 5M15 4c0 2 2 2 3 4s3 2 2 4" fill="none" stroke="var(--icon-cut)" stroke-width="1.6"/></svg>
      </li>
      <li class="contact-item">
        <span>842 E Alder Ave, Halden Falls, MN 43827</span>
        <svg class="contact-icon" viewBox="0 0 24 24" aria-hidden="true"><path d="M12 2a7 7 0 0 0-7 7c0 5.2 7 13 7 13s7-7.8 7-13a7 7 0 0 0-7-7zm0 9.5A2.5 2.5 0 1 1 12 6.5a2.5 2.5 0 0 1 0 5z"/></svg>
      </li>
    </ul>
    <div class="accent-green"></div>
    <div class="accent-navy"></div>
  </section>

  <section class="card card-back" role="img" aria-label="Repeating diagonal brand name pattern on violet"></section>
</main>
</body>
</html>
```